Computer consultant business card

Bexil Software is a newly started computer consulting company. It's a small one-man company that provides mostly Vornix applications but also websites in collaboration with designers. I'm running this company on the side of full time university studies.

I want the final design to be clean and memorable. Be creative! :)

Some inspiration:
http://www.pixelmarta.com/design/48317
http://www.pixelmarta.com/design/2739164/business-card-design-by-frostlynk
http://www.pixelmarta.com/design/604281/business-card-design-by-koralind-vestrabanu

See attachment for my company logo.
Updates

I would like to thank everyone for submitting! I'll need a couple of days to review and ultimately select a design.

Target Market(s)

Non-technical entrepreneurs and small companies.

Industry/Entity Type

University

Requirements
Must have
• My company logo.
In any way, both colors from my logo.
First- and last name, e-mail and phone number.
Double-sided design.
Nice to have
• Something creative with the symbol in my logo

```html
<!DOCTYPE html>
<html lang="en">
<head>
<meta charset="utf-8">
<title>Bexil Software – Business Card</title>
<link rel="stylesheet" href="https://fonts.googleapis.com/css2?family=Arimo:wght@400;700&family=Cinzel:wght@400&family=Oswald:wght@600&family=Tinos&display=swap">
<style>
  :root {
    --stage: #e6e8ec;
    --paper: #ffffff;
    --ink-dark: #3d3d3f;
    --ink-mid: #6b6b6e;
    --ink-soft: #8a8a8d;
    --brand-blue: #4a76c0;
    --back-deep: #1f3c78;
    --back-light: #6f95c9;
  }
  * { margin: 0; padding: 0; box-sizing: border-box; }
  html, body { width: 1200px; height: 900px; overflow: hidden; }
  body {
    background: var(--stage);
    display: flex;
    flex-direction: column;
    align-items: center;
    justify-content: center;
    gap: 60px;
    font-family: "Arimo", Arial, sans-serif;
  }
  .card {
    position: relative;
    width: 620px;
    height: 354px;
    box-shadow: 0 10px 28px rgba(20, 30, 50, 0.22);
    overflow: hidden;
  }
  .card-front { background: var(--paper); }
  .card-back {
    background: radial-gradient(ellipse at 35% 70%, var(--back-light) 0%, #3d64a6 45%, var(--back-deep) 100%);
  }

  /* Front: identity */
  .identity {
    position: absolute;
    top: 38px;
    right: 44px;
    text-align: left;
  }
  .identity-name {
    font-family: "Oswald", "Arial Narrow", sans-serif;
    font-weight: 600;
    font-size: 24px;
    letter-spacing: 0.5px;
    color: var(--ink-mid);
    line-height: 1.1;
  }
  .identity-role {
    font-family: "Tinos", "Times New Roman", serif;
    font-size: 12px;
    color: var(--ink-soft);
  }

  /* Front: contact list */
  .contact-list {
    position: absolute;
    top: 178px;
    right: 44px;
    list-style: none;
  }
  .contact-item {
    display: flex;
    align-items: center;
    gap: 10px;
    font-size: 13px;
    color: var(--ink-dark);
    line-height: 19px;
  }
  .contact-icon { width: 11px; height: 11px; fill: var(--brand-blue); flex: none; }

  /* Front: brand block */
  .brand {
    position: absolute;
    left: 40px;
    bottom: 54px;
    display: flex;
    align-items: flex-end;
    gap: 16px;
  }
  .brand-dot {
    width: 56px;
    height: 56px;
    border-radius: 50%;
    background: var(--brand-blue);
    margin-bottom: 6px;
  }
  .brand-name {
    font-family: "Arimo", Arial, sans-serif;
    font-weight: 700;
    font-size: 50px;
    line-height: 0.9;
    color: var(--ink-dark);
    letter-spacing: 1px;
  }
  .brand-title {
    font-family: "Cinzel", "Times New Roman", serif;
    font-size: 20px;
    line-height: 1.05;
    color: var(--ink-mid);
    letter-spacing: 2px;
    margin-top: 6px;
  }

  /* Back */
  .back-brand {
    position: absolute;
    inset: 0;
    display: flex;
    align-items: center;
    justify-content: center;
    gap: 28px;
  }
  .back-dot {
    width: 120px;
    height: 120px;
    border-radius: 50%;
    background: var(--paper);
  }
  .back-name {
    font-family: "Arimo", Arial, sans-serif;
    font-weight: 700;
    font-size: 104px;
    color: var(--ink-dark);
    letter-spacing: 2px;
  }
</style>
</head>
<body>

  <section class="card card-front" aria-label="Card front">
    <div class="identity">
      <p class="identity-name">ELAN MORIS</p>
      <p class="identity-role">Graphic Designer</p>
    </div>

    <ul class="contact-list">
      <li class="contact-item">
        <svg class="contact-icon" viewBox="0 0 12 12" aria-hidden="true"><path d="M2.5 0.5h2l1 3-1.5 1a6 6 0 0 0 3.5 3.5l1-1.5 3 1v2a1.5 1.5 0 0 1-1.5 1.5A10 10 0 0 1 1 2a1.5 1.5 0 0 1 1.5-1.5z"/></svg>
        +(000) 1234 5678
      </li>
      <li class="contact-item">
        <svg class="contact-icon" viewBox="0 0 12 12" aria-hidden="true"><path d="M3 0h6v3H3zM0 4h12v6h-2v2H2v-2H0zM3 8v3h6V8z"/></svg>
        +(000) 1234 5679
      </li>
      <li class="contact-item">
        <svg class="contact-icon" viewBox="0 0 12 12" aria-hidden="true"><path d="M0 2h12v8H0zM1 3v.4l5 3.4 5-3.4V3zM1 4.6V9h10V4.6L6 8z"/></svg>
        email@yourdomain.com
      </li>
      <li class="contact-item">
        <svg class="contact-icon" viewBox="0 0 12 12" aria-hidden="true"><path d="M6 0a6 6 0 1 0 0 12A6 6 0 0 0 6 0zm0 1.2c.7.8 1.2 2.2 1.3 3.8H4.7C4.8 3.4 5.3 2 6 1.2zM1.3 6h2.4c.1 1.6.5 3 1.1 4A4.8 4.8 0 0 1 1.3 6zm3.4 0h2.6C7.2 7.7 6.7 9.1 6 10.8 5.3 9.1 4.8 7.7 4.7 6zm3.6 0h2.4a4.8 4.8 0 0 1-3.5 4c.6-1 1-2.4 1.1-4z"/></svg>
        www.yourwebsite.com
      </li>
    </ul>

    <div class="brand">
      <div class="brand-dot"></div>
      <div>
        <p class="brand-name">bexil</p>
        <p class="brand-title">MANAGING<br>DIRECTOR</p>
      </div>
    </div>
  </section>

  <section class="card card-back" aria-label="Card back">
    <div class="back-brand">
      <div class="back-dot"></div>
      <p class="back-name">bexil</p>
    </div>
  </section>

</body>
</html>
```